Web Design Project

We wish to create a web based logistics exchange for heavy machinery and equipment catering to the mining, oil, gas and infrastructure industries. Customers interested in shipping equipment can post a load on the site and this would then be auctioned off through an online auction to prospective transport providers.Payments would be through direct bank transfer,pelko, quorvantix etc.
Both shippers and transport providers gain access via membership.
When a load is posted it would appear on the map indicating its location.Transport providers click on the icon of this map to access information of the pick up and delivery details as well as the load description.
The site would also have links to transport departments and equipment specification sites.
Advertising and merchandising are the other areas of revenue through the site

Target Market(s)

Shippers from Machinery Auction centres and Transport companies

Industry/Entity Type

Catering

Requirements
Must have
• The Logo of the company. The file is attached.

```html
<!DOCTYPE html>
<html lang="en">
<head>
<meta charset="utf-8">
<title>Tarrak Freight — Freight Management</title>
<link rel="stylesheet" href="https://fonts.googleapis.com/css2?family=Exo:wght@400;500&family=Hind:wght@400;500&display=swap">
<style>
  :root {
    --navy: #0d3a78;
    --blue: #1a62b4;
    --blue-mid: #2a78c8;
    --blue-light: #5aa0e0;
    --link: #1f4f96;
    --text: #333333;
    --rule: #d7dbe0;
    --panel: #f4f5f7;
    --white: #ffffff;
    --icon-grey: #6e7074;
  }
  * { box-sizing: border-box; margin: 0; padding: 0; }
  html, body { width: 1200px; height: 900px; overflow: hidden; }
  body { position: relative; background: var(--white); font-family: "Hind", sans-serif; color: var(--text); font-size: 9.5px; line-height: 11px; }
  .heading { font-family: "Exo", sans-serif; text-transform: uppercase; letter-spacing: .3px; }

  .site-header { position: absolute; left: 0; top: 0; width: 1200px; height: 92px; }
  .brand { position: absolute; left: 280px; top: 24px; display: flex; align-items: center; gap: 10px; }
  .brand-mark { width: 26px; height: 26px; background: var(--blue); }
  .brand-name { font-family: "Exo", sans-serif; font-weight: 500; font-size: 21px; line-height: 21px; color: #2b2e33; letter-spacing: 1px; }
  .account-links { position: absolute; left: 780px; top: 28px; font-family: "Exo", sans-serif; font-size: 10px; color: var(--link); }
  .account-links span { margin: 0 5px; color: #9aa; }
  .search { position: absolute; left: 779px; top: 51px; display: flex; align-items: center; gap: 6px; }
  .search-field { width: 124px; height: 18px; border: 1px solid #8aa6c8; border-radius: 4px; background: #fff; box-shadow: inset 0 1px 2px rgba(0,0,0,.15); }

  .main-nav { position: absolute; left: 0; top: 92px; width: 1200px; height: 27px; background: linear-gradient(#ffffff, #e6e7e9); border-top: 1px solid #dadada; border-bottom: 1px solid #cfd2d6; }
  .main-nav ul { position: absolute; left: 280px; display: flex; list-style: none; height: 26px; }
  .main-nav li { font-family: "Exo", sans-serif; font-size: 11px; color: var(--link); line-height: 26px; padding: 0 16px 0 21px; border-right: 1px solid #d3d6da; text-transform: uppercase; }
  .main-nav li:last-child { border-right: none; }

  .hero { position: absolute; left: 0; top: 119px; width: 1200px; height: 183px; background: linear-gradient(180deg, #1f6fc4 0%, #4c97d6 45%, #6fb3e4 70%, #3d88cc 100%); }

  .feature-band { position: absolute; left: 0; top: 302px; width: 1200px; height: 23px; background: linear-gradient(#3a86d0, #1e5fae); }
  .feature-tabs { position: absolute; left: 280px; top: 302px; display: flex; }
  .feature-tabs div { height: 23px; line-height: 24px; padding-left: 12px; font-size: 10px; color: var(--white); border-right: 1px solid #5b9bd8; }

  .features { position: absolute; left: 280px; top: 325px; width: 643px; height: 100px; display: flex; border: 1px solid var(--rule); border-top: none; border-radius: 0 0 4px 4px; background: linear-gradient(#ffffff, var(--panel)); }
  .feature { position: relative; padding: 12px 12px 0; border-right: 1px solid var(--rule); }
  .feature:last-child { border-right: none; }
  .feature h3 { font-size: 12px; font-weight: 400; color: #333; margin-bottom: 10px; margin-top: 1px; }
  .feature ul { list-style: none; }
  .feature li::before { content: "• "; }
  .read-more { position: absolute; right: 16px; bottom: 9px; font-family: "Exo", sans-serif; font-size: 10px; color: var(--link); text-transform: uppercase; }

  .intro { position: absolute; left: 280px; top: 438px; width: 412px; }
  .intro h1 { font-size: 16px; line-height: 18px; font-weight: 500; color: var(--navy); margin-bottom: 11px; }
  .intro h2 { font-size: 10px; font-weight: 500; color: var(--link); margin-top: 10px; line-height: 12px; }

  .sidebar { position: absolute; left: 708px; top: 437px; width: 215px; }
  .map-card { position: relative; height: 80px; border-radius: 4px; overflow: hidden; background: linear-gradient(135deg, #f1e6c8, #e9d9a8 50%, #d9e2ea); }
  .map-card .caption { position: absolute; left: 0; bottom: 0; width: 100%; height: 28px; background: rgba(90,160,224,.85); color: #fff; font-size: 11px; line-height: 30px; padding-left: 12px; }
  .panel { margin-top: 6px; border-radius: 4px; padding: 10px 14px 0; color: var(--white); }
  .news { height: 139px; background: linear-gradient(#2e5f9c, #12407f); }
  .signup { height: 76px; background: linear-gradient(#3a86d0, #1e62b0); }
  .panel h3 { font-size: 12px; font-weight: 400; padding-bottom: 6px; border-bottom: 1px solid rgba(255,255,255,.7); margin-bottom: 12px; }
  .news-item { font-size: 9.5px; line-height: 10px; margin-bottom: 12px; }
  .news-item span { display: block; font-size: 7.5px; color: #8db3e0; }
  .signup-row { display: flex; gap: 8px; }
  .signup-field { width: 123px; height: 19px; border-radius: 3px; background: #fff; }
  .signup-btn { width: 54px; height: 19px; border-radius: 4px; background: linear-gradient(#ffffff, #c9ced4); color: var(--link); font-size: 9px; text-align: center; line-height: 20px; }

  .site-footer { position: absolute; left: 0; top: 757px; width: 1200px; height: 143px; background: linear-gradient(#0c3a7a, #2e5a96); color: #fff; }
  .footer-col { position: absolute; top: 15px; width: 181px; }
  .footer-col h4 { font-size: 11px; font-weight: 400; padding-bottom: 8px; border-bottom: 1px solid rgba(255,255,255,.6); margin-bottom: 10px; }
  .footer-col li { list-style: none; font-size: 9.5px; line-height: 15.4px; letter-spacing: .3px; }
  .social { position: absolute; left: 791px; top: 19px; display: flex; gap: 4px; }
  .social span { width: 23px; height: 23px; background: var(--icon-grey); }
  .copyright { position: absolute; left: 827px; top: 58px; font-size: 9.5px; }
</style>
</head>
<body>
  <header class="site-header">
    <div class="brand">
      <span class="brand-mark"></span>
      <span class="brand-name">TARRAK<br>FREIGHT</span>
    </div>
    <div class="account-links">SIGN IN<span>|</span>REGISTER</div>
    <div class="search">
      <div class="search-field"></div>
      <svg width="16" height="16" viewBox="0 0 16 16"><circle cx="6" cy="6" r="4.5" fill="none" stroke="#777" stroke-width="1.6"/><line x1="9.5" y1="9.5" x2="14.5" y2="14.5" stroke="#777" stroke-width="2"/></svg>
    </div>
  </header>

  <nav class="main-nav">
    <ul>
      <li>Home</li><li>About Us</li><li>Clients</li><li>Reports</li><li>Services</li><li>Support</li><li>Map</li><li>Contact Us</li>
    </ul>
  </nav>

  <div class="hero" role="img" aria-label="Tipper truck and excavator working on a rocky shore beside calm blue water"></div>

  <div class="feature-band"></div>
  <div class="feature-tabs heading">
    <div style="width:214px">Why Tarrak?</div>
    <div style="width:214px">What is Tarrak?</div>
    <div style="width:215px;border-right:none">What our clients say</div>
  </div>

  <section class="features">
    <div class="feature" style="width:214px">
      <h3 class="heading">Save time, save money</h3>
      <ul><li>Sed ut perspiciatis.</li><li>Nemo enim ipsam.</li><li>Neque porro quisquam.</li><li>Ut enim ad minima.</li></ul>
      <span class="read-more">Read more</span>
    </div>
    <div class="feature" style="width:214px">
      <p>Ut enim ad minima veniam, quis nostrum exercitationem ullam corporis suscipit laboriosam, nisi ut aliquid ex ea commodi consequatur? Quis autem vel eum iure reprehenderit qui in ea fugiat quo voluptas nulla pariatur...</p>
      <span class="read-more">Read more</span>
    </div>
    <div class="feature" style="width:215px">
      <p>Effortless. All of the tools you need to manage the most challenging aspect of any business. I have turned to TARRAK for valuable information on how to...</p>
      <span class="read-more">Read more</span>
    </div>
  </section>

  <main class="intro">
    <h1 class="heading">Welcome to Tarrak<br>The only freight management<br>solution you will ever need</h1>
    <p>Sed ut perspiciatis unde omnis iste natus error sit voluptatem accusantium doloremque laudantium, totam rem aperiam, eaque ipsa quae ab illo inventore veritatis et quasi architecto beatae vitae dicta sunt explicabo. Nemo enim ipsam voluptatem quia voluptas sit aspernatur aut odit aut fugit, sed quia consequuntur magni dolores eos qui ratione voluptatem sequi nesciunt.</p>
    <h2 class="heading">What we do</h2>
    <p>Neque porro quisquam est, qui dolorem ipsum quia dolor sit amet, consectetur, adipisci velit, sed quia non numquam eius modi tempora incidunt ut labore et dolore magnam aliquam quaerat voluptatem. Ut enim ad minima veniam, quis nostrum exercitationem ullam corporis suscipit laboriosam, nisi ut aliquid ex ea commodi consequatur? Quis autem vel eum iure reprehenderit qui in ea voluptate velit esse quam nihil molestiae consequatur, vel illum qui dolorem eum fugiat quo voluptas nulla pariatur?</p>
    <h2 class="heading">How to join</h2>
    <p>Ut enim ad minima veniam, quis nostrum exercitationem ullam corporis suscipit laboriosam, nisi ut aliquid ex ea commodi consequatur? Quis autem vel eum iure reprehenderit qui in ea voluptate velit esse quam nihil molestiae consequatur.</p>
    <h2 class="heading">Report</h2>
    <p>Nemo enim ipsam voluptatem quia voluptas sit aspernatur aut odit aut fugit, sed quia consequuntur magni dolores eos qui ratione voluptatem sequi nesciunt.</p>
  </main>

  <aside class="sidebar">
    <div class="map-card" role="img" aria-label="Street map of the city showing posted load locations">
      <div class="caption heading">Interactive map</div>
    </div>
    <div class="panel news">
      <h3 class="heading">Latest news</h3>
      <div class="news-item">August 2012 Newsletter.<span>READ MORE</span></div>
      <div class="news-item">TARRAK forms Strategic Relationship...<span>READ MORE</span></div>
      <div class="news-item">TARRAK signs new high profile client...<span>READ MORE</span></div>
    </div>
    <div class="panel signup">
      <h3 class="heading">Sign up for our newsletter</h3>
      <div class="signup-row"><div class="signup-field"></div><div class="signup-btn heading">Sign up</div></div>
    </div>
  </aside>

  <footer class="site-footer">
    <div class="footer-col" style="left:286px">
      <h4 class="heading">Information</h4>
      <ul><li>Terms &amp; Conditions</li><li>Frequently Asked Questions</li></ul>
    </div>
    <div class="footer-col" style="left:507px">
      <h4 class="heading">Affiliates</h4>
      <ul><li>Quis Autem</li><li>Nemoenim</li><li>Sedquia</li><li>Fugiat</li><li>Magni Dolores</li></ul>
    </div>
    <div class="social" aria-label="Social links"><span></span><span></span><span></span><span></span><span></span></div>
    <p class="copyright">Copyright Tarrak 2012</p>
  </footer>
</body>
</html>
```